Corporate Business Card

Very professional, Modern, Not to busy, include phone address email, website
(555) 617-4930, 18761 52nd Avenue S, Millbrook, OR 98047, martin@plumlinegroup.com, varkoworks.com

Target Market(s)

Manufacturing

Industry/Entity Type

Aero, machining, manufacturing, Off road racing

Contact Information for Business Card

Phone, address email, website

```html
<!DOCTYPE html>
<html lang="en">
<head>
<meta charset="utf-8">
<title>Varko Works – Business Card</title>
<link rel="stylesheet" href="https://fonts.googleapis.com/css2?family=Quicksand:wght@500;700&display=swap">
<style>
  :root {
    --navy: #1b3a6f;
    --red: #d42a2f;
    --paper: #ffffff;
    --pattern: #e6e9f0;
    --pattern-soft: #f1f3f7;
    --icon-ink: #ffffff;
  }
  html, body {
    margin: 0;
    padding: 0;
    width: 1200px;
    height: 686px;
    overflow: hidden;
    background: var(--paper);
  }
  .card {
    position: relative;
    width: 1200px;
    height: 686px;
    background: var(--paper);
    overflow: hidden;
    font-family: "Quicksand", sans-serif;
    font-weight: 500;
    color: var(--navy);
  }
  .pattern-band {
    position: absolute;
    inset: 0;
  }
  .brand-name {
    position: absolute;
    left: 60px;
    top: 88px;
    margin: 0;
    font-size: 58px;
    line-height: 1;
    font-weight: 700;
    letter-spacing: 0.5px;
    color: var(--navy);
    white-space: nowrap;
  }
  .contact-icons {
    position: absolute;
    left: 60px;
    top: 365px;
  }
  .contact-list {
    position: absolute;
    left: 67px;
    top: 460px;
    margin: 0;
    padding: 0;
    list-style: none;
    font-size: 27px;
    line-height: 42px;
    letter-spacing: 0.2px;
    white-space: nowrap;
  }
</style>
</head>
<body>
<div class="card">
  <svg class="pattern-band" width="1200" height="686" viewBox="0 0 1200 686">
    <defs>
      <linearGradient id="band-tone" x1="0" y1="0" x2="1" y2="0">
        <stop offset="0" stop-color="var(--pattern-soft)"/>
        <stop offset="1" stop-color="var(--pattern)"/>
      </linearGradient>
    </defs>
    <polygon role="img" aria-label="Faint repeated diagonal brand name pattern"
             points="594,686 891,0 1200,0 1200,686" fill="url(#band-tone)"/>
  </svg>

  <h1 class="brand-name">Varko Works</h1>

  <svg class="contact-icons" width="340" height="64" viewBox="0 0 340 64" aria-label="Contact icons">
    <line x1="31" y1="32" x2="276" y2="32" stroke="var(--red)" stroke-width="3"/>
    <g class="icon-phone">
      <circle cx="31" cy="32" r="25" fill="var(--red)"/>
      <path d="M22 20 l5 -2 l4 8 l-3 3 q3 6 8 9 l3 -3 l8 4 l-2 5 q-2 3 -7 1 q-12 -5 -17 -18 q-1 -5 1 -7z" fill="var(--icon-ink)"/>
      <path d="M35 20 q6 1 8 7 M35 15 q10 1 13 11" stroke="var(--icon-ink)" stroke-width="2" fill="none" stroke-linecap="round"/>
    </g>
    <g class="icon-mail">
      <circle cx="111" cy="32" r="25" fill="var(--red)"/>
      <rect x="98" y="23" width="26" height="18" rx="1.5" fill="none" stroke="var(--icon-ink)" stroke-width="2.4"/>
      <path d="M98 24 l13 10 l13 -10 M98 40 l9 -8 M124 40 l-9 -8" stroke="var(--icon-ink)" stroke-width="2" fill="none"/>
    </g>
    <g class="icon-pin">
      <circle cx="194" cy="32" r="25" fill="var(--red)"/>
      <path d="M194 47 q-10 -11 -10 -19 a10 10 0 0 1 20 0 q0 8 -10 19z" fill="none" stroke="var(--icon-ink)" stroke-width="2.4"/>
      <circle cx="194" cy="28" r="3.5" fill="var(--icon-ink)"/>
      <path d="M186 48 h16" stroke="var(--icon-ink)" stroke-width="2" stroke-linecap="round"/>
    </g>
    <g class="icon-globe" fill="none" stroke="var(--icon-ink)" stroke-width="2">
      <circle cx="276" cy="32" r="25" fill="var(--red)" stroke="none"/>
      <circle cx="276" cy="32" r="12"/>
      <ellipse cx="276" cy="32" rx="5.5" ry="12"/>
      <path d="M264 32 h24 M266 25 h20 M266 39 h20 M276 20 v24"/>
    </g>
  </svg>

  <ul class="contact-list">
    <li class="contact-phone">(555) 617-4930, 18761</li>
    <li class="contact-web">varkoworks.com</li>
    <li class="contact-address">52nd Avenue S, Millbrook, OR 98047</li>
    <li class="contact-email">martin@plumlinegroup.com</li>
  </ul>
</div>
</body>
</html>
```